Public Relations Agency Seeks Wordpress Design and Coding

TRELVOX Studio is a public relations agency specializing in media relations, public affairs and marketing communication.

The site should display the following visual characteristics: professionalism, trustworthiness, high-tech focus, clear and concise design.

The desired colors are royal blue, gray and hints of red.

Design look/feel inspired by this site: http://brightpathgatherings.example/

Specifications:

1. Navigation/Pages/Index:

HOME

ABOUT US

SERVICES

NEWS

CONTACT

---

2. Functionality of/content for each page:

- Home
o Dominant photo (professional, edgy, innovative)
o Simple, straightforward access to/from “Home” from other pages
o Includes logo (attached) and tagline "Unleash the power of communication"
o Direct link to “CONTACT”
o Links to social media accounts: Facebook, Twitter, LinkedIn

- About Us

o Company profile blurb
o President’s photo with short bio

- Services
o Public Relations
 Strategic communication
 Brand and reputation management
 Community relations
o Media Relations
 News coverage and contacts
 Media training and interview skills
 Crisis communications
o Congressional Affairs
 Public affairs
 Public policy
 Legislative strategy
o Mass Communication
 Speechwriting
 Presentation creation
 Social media
o Marketing Communications
 Business collateral material
 Promotional campaigns
 Special events and tradeshows

- News
o Blog-like page to post information and/or share news from other sites

- Contact
o Standard “Contact Us” form (Name, Email, Phone, Message)
o Direct Contact
 (407) 555-0164
 Marisol@TRELVOXstudio.example

Target Market(s)

Small to large businesses specializing in high technology, defense/military, medicine/healthcare, and wide array of professional services.

Industry/Entity Type

Marketing

Font styles to use
Serif
Sans Serif

Colors
0555a3
ec2027
edf3f7

Requirements
Must have
• -- Project reqires DESIGN - and - fully CODED.

-- Strong SEO

-- Optimized for mobile viewing

Thank you!

```html
<!DOCTYPE html>
<html lang="en">
<head>
<meta charset="utf-8">
<title>TRELVOX Studio – Public Relations Agency</title>
<link rel="stylesheet" href="https://fonts.googleapis.com/css2?family=Josefin+Sans:wght@400;600;700&family=Open+Sans:wght@400;600;700&display=swap">
<style>
:root{
  --royal:#0555a3;
  --royal-deep:#04468a;
  --red:#ec2027;
  --mist:#edf3f7;
  --ink:#333a42;
  --muted:#7a828b;
  --line:#d9dee3;
  --footer:#2b2e33;
  --footer-deep:#222427;
  --white:#ffffff;
}
*{box-sizing:border-box;margin:0;padding:0}
html,body{width:1200px;height:2732px;overflow:hidden}
body{font-family:"Open Sans",Arial,sans-serif;color:var(--ink);background:var(--white);font-size:15px;line-height:1.6}
section,header,footer{overflow:hidden}
.heading{font-family:"Josefin Sans","Open Sans",sans-serif;font-weight:600;letter-spacing:1px;text-transform:uppercase}
.section-title{font-size:26px;line-height:1.3;text-align:center;position:relative;padding-bottom:14px}
.section-title::after{content:"";position:absolute;left:50%;bottom:0;width:50px;height:3px;margin-left:-25px;background:var(--red)}
.on-blue{color:var(--white)}

/* header */
.site-header{height:100px;display:flex;align-items:center;justify-content:space-between;padding:0 180px;background:var(--white)}
.brand{font-family:"Open Sans",sans-serif;font-weight:700;font-size:30px;color:var(--royal);letter-spacing:1px}
.main-nav{display:flex;gap:6px}
.main-nav a{font-size:13px;font-weight:600;color:var(--ink);text-decoration:none;padding:10px 16px;text-transform:uppercase}
.main-nav a.active{background:var(--red);color:var(--white)}

/* hero */
.hero{position:relative;height:500px}
.hero-tagline{position:absolute;right:210px;top:205px;font-size:44px;line-height:1.15;color:var(--ink);width:430px}
.hero-dots{position:absolute;left:50%;bottom:22px;transform:translateX(-50%);display:flex;gap:10px}
.hero-dots span{width:12px;height:12px;border-radius:50%;background:var(--royal)}
.hero-dots span.current{background:var(--red)}

/* about */
.about{height:220px;background:var(--royal);padding:30px 180px 0}
.about p{color:#dce7f3;font-size:13px;text-align:center;margin-top:22px;line-height:1.7}

/* focus */
.focus{height:270px;display:flex;justify-content:center;gap:100px;padding-top:38px}
.focus-item{width:240px;text-align:center}
.focus-photo{width:130px;height:130px;border-radius:50%;margin:0 auto 14px}
.focus-item h3{font-size:17px;color:var(--royal);font-weight:600;line-height:1.4}
.focus-item p{font-size:12px;color:var(--muted);line-height:1.5;margin-top:4px}

/* services */
.services{height:350px;background:var(--royal);padding:32px 180px 0}
.service-grid{display:grid;grid-template-columns:repeat(3,1fr);gap:28px 40px;margin-top:30px}
.service h4{display:flex;align-items:center;gap:10px;font-size:12px;color:var(--white);font-weight:700;text-transform:uppercase}
.service p{font-size:11.5px;color:#c8d8ea;line-height:1.6;margin-top:8px;padding-left:34px}

/* team */
.team{height:360px;padding:32px 180px 0;text-align:center}
.team-slider{display:flex;align-items:center;justify-content:center;gap:70px;margin-top:22px}
.arrow{width:24px;height:24px}
.member-photo{width:110px;height:110px;border-radius:50%;background:radial-gradient(circle at 50% 40%,#e7c3a3,#b98a5c 70%,#8e6a48);margin:0 auto}
.member-name{font-size:12px;color:var(--red);font-weight:700;margin-top:8px;letter-spacing:1px;line-height:1.4}
.team p{font-size:12.5px;color:var(--muted);margin-top:12px;line-height:1.7}

/* news */
.news{height:400px;background:var(--royal);padding:32px 180px 0}
.news-grid{display:flex;gap:30px;margin-top:32px}
.news-card{width:260px;flex:1;position:relative}
.news-image{height:220px}
.news-meta{position:absolute;left:0;right:0;top:196px;display:flex;justify-content:space-between;padding:0 12px}
.news-meta span{background:var(--red);color:var(--white);font-size:11px;font-weight:700;padding:4px 10px}
.news-card p{color:#dce7f3;font-size:12px;line-height:1.5;margin-top:12px}

/* contact */
.contact{height:380px;padding:28px 180px 0}
.contact-body{display:flex;gap:70px;margin-top:30px}
.contact-form{width:480px;display:grid;grid-template-columns:1fr 1fr;gap:12px 16px}
.field{height:34px;border:1px solid var(--line);display:flex;align-items:center;gap:8px;padding:0 10px;font-size:11px;color:var(--muted);text-transform:uppercase}
.field.message{grid-column:1 / 3;height:120px;align-items:flex-start;padding-top:8px}
.submit{grid-column:1 / 3;justify-self:center;width:220px;height:34px;background:var(--red);color:var(--white);border:0;font-size:13px;font-weight:700;letter-spacing:1px}
.contact-info{font-size:13px;color:var(--muted)}
.contact-info .lead{margin-bottom:20px}
.contact-line{display:flex;align-items:center;gap:12px;margin-bottom:18px}

/* footer */
.site-footer{height:152px;background:var(--footer);position:relative}
.social{display:flex;justify-content:center;gap:16px;padding-top:34px}
.social span{width:34px;height:34px;border-radius:50%;background:var(--royal)}
.footer-bar{position:absolute;left:0;right:0;bottom:0;height:44px;background:var(--footer-deep);display:flex;align-items:center;justify-content:space-between;padding:0 180px;font-size:11px;color:#9aa0a6}
</style>
</head>
<body>

<header class="site-header">
  <div class="brand">TRELVOX Studio</div>
  <nav class="main-nav">
    <a class="active" href="#">Home</a>
    <a href="#">About Us</a>
    <a href="#">Services</a>
    <a href="#">News</a>
    <a href="#">Contact Us</a>
  </nav>
</header>

<section class="hero">
  <div role="img" aria-label="Photo of a child shouting through a megaphone against a pale wall" style="position:absolute;inset:0;background:linear-gradient(90deg,#b9ad9c 0%,#d8d0c3 40%,#ece7de 100%)"></div>
  <h1 class="hero-tagline heading">Unleash the power of communication</h1>
  <div class="hero-dots"><span class="current"></span><span></span><span></span></div>
</section>

<section class="about">
  <h2 class="section-title heading on-blue">About Us</h2>
  <p>We help organizations tell their story with clarity and purpose. Our team builds lasting media connections, shapes public perception and plans campaigns that reach the right audience at the right time. From emerging technology firms to healthcare and defense leaders, clients trust us to deliver measured, strategic communication that earns attention and protects reputation. Every message is crafted with care, grounded in research and delivered with precision across every channel.</p>
</section>

<section class="focus">
  <div class="focus-item">
    <div class="focus-photo" role="img" aria-label="Photo of a press microphone" style="background:radial-gradient(circle,#9aa3ab,#4b535b)"></div>
    <h3>Media Relations</h3>
    <p>Trusted press contacts and coverage that puts your story in front of readers.</p>
  </div>
  <div class="focus-item">
    <div class="focus-photo" role="img" aria-label="Photo of two silhouettes shaking hands against a blue sky" style="background:radial-gradient(circle,#7fb3e0,#1f5f9e)"></div>
    <h3>Public Affairs</h3>
    <p>Clear policy messaging that connects you with decision makers and community.</p>
  </div>
  <div class="focus-item">
    <div class="focus-photo" role="img" aria-label="Photo of a hand placing marketing blocks" style="background:radial-gradient(circle,#d7d7d7,#5a5a5a)"></div>
    <h3>Marketing Communication</h3>
    <p>Campaigns, collateral and events that bring your brand to the market.</p>
  </div>
</section>

<section class="services">
  <h2 class="section-title heading on-blue">Our Services</h2>
  <div class="service-grid">
    <div class="service">
      <h4><svg width="24" height="24" viewBox="0 0 24 24" fill="#fff"><path d="M3 10h4l9-5v14l-9-5H3z"/><rect x="6" y="14" width="3" height="6"/></svg>Public Relations</h4>
      <p>Strategic communication, brand and reputation management and community relations.</p>
    </div>
    <div class="service">
      <h4><svg width="24" height="24" viewBox="0 0 24 24" fill="none" stroke="#fff" stroke-width="2.4"><path d="M4 20l9-9M14 4l6 6M11 7l6 6"/></svg>Media Relations</h4>
      <p>News coverage and contacts, media training, interview skills and crisis work.</p>
    </div>
    <div class="service">
      <h4><svg width="24" height="24" viewBox="0 0 24 24" fill="#fff"><rect x="3" y="4" width="18" height="4"/><rect x="3" y="10" width="18" height="4"/><rect x="3" y="16" width="18" height="4"/></svg>Congressional Affairs</h4>
      <p>Public affairs, public policy and legislative strategy for every stakeholder.</p>
    </div>
    <div class="service">
      <h4><svg width="24" height="24" viewBox="0 0 24 24" fill="#fff"><circle cx="12" cy="12" r="9"/><circle cx="12" cy="12" r="4" fill="#0555a3"/></svg>Mass Communication</h4>
      <p>Speechwriting, presentation creation and social media that keeps voices heard.</p>
    </div>
    <div class="service">
      <h4><svg width="24" height="24" viewBox="0 0 24 24" fill="#fff"><rect x="3" y="6" width="18" height="13"/><rect x="8" y="3" width="8" height="4"/></svg>Marketing Communications</h4>
      <p>Business collateral, promotional campaigns, special events and tradeshows.</p>
    </div>
    <div class="service">
      <h4><svg width="24" height="24" viewBox="0 0 24 24" fill="#fff"><rect x="3" y="3" width="8" height="8"/><rect x="13" y="3" width="8" height="8"/><rect x="3" y="13" width="8" height="8"/><rect x="13" y="13" width="8" height="8"/></svg>Strategic Planning</h4>
      <p>Research, audience insight and measured plans that guide every campaign.</p>
    </div>
  </div>
</section>

<section class="team">
  <h2 class="section-title heading">Our Team</h2>
  <div class="team-slider">
    <svg class="arrow" viewBox="0 0 24 24" fill="none" stroke="#7a828b" stroke-width="2.5"><path d="M15 4l-8 8 8 8"/></svg>
    <div>
      <div class="member-photo" role="img" aria-label="Portrait photo of the agency president"></div>
      <div class="member-name">MARISOL</div>
    </div>
    <svg class="arrow" viewBox="0 0 24 24" fill="none" stroke="#7a828b" stroke-width="2.5"><path d="M9 4l8 8-8 8"/></svg>
  </div>
  <p>Our president brings two decades of agency and newsroom experience, guiding clients in technology, defense and healthcare through launches, policy debates and critical moments. She leads every account personally and believes honest, well prepared communication is the strongest asset any organization can hold.</p>
</section>

<section class="news">
  <h2 class="section-title heading on-blue">Latest News</h2>
  <div class="news-grid">
    <article class="news-card">
      <div class="news-image" role="img" aria-label="Illustration of colourful speech bubbles" style="background:linear-gradient(135deg,#5fc3e4,#2a8fc7)"></div>
      <div class="news-meta"><span>SEP 26 2014</span><span>READ MORE</span></div>
      <p>New media season opens with fresh coverage plans for our technology clients.</p>
    </article>
    <article class="news-card">
      <div class="news-image" role="img" aria-label="Photo of many raised hands in colourful light" style="background:linear-gradient(135deg,#1b1b2b,#6a2f7a 60%,#d9a21b)"></div>
      <div class="news-meta"><span>SEP 26 2014</span><span>READ MORE</span></div>
      <p>Community relations forum draws local leaders and business partners together.</p>
    </article>
    <article class="news-card">
      <div class="news-image" role="img" aria-label="Illustration of many multicoloured speech bubbles" style="background:linear-gradient(135deg,#f2f2f2,#e9b34a 45%,#4a9fd8)"></div>
      <div class="news-meta"><span>SEP 26 2014</span><span>READ MORE</span></div>
      <p>Five practical tips to prepare your team for its next media interview.</p>
    </article>
  </div>
</section>

<section class="contact">
  <h2 class="section-title heading">Contact Us</h2>
  <div class="contact-body">
    <form class="contact-form">
      <div class="field"><svg width="12" height="12" viewBox="0 0 24 24" fill="#7a828b"><circle cx="12" cy="7" r="5"/><path d="M2 23c0-6 4-9 10-9s10 3 10 9z"/></svg>Name</div>
      <div class="field"><svg width="12" height="12" viewBox="0 0 24 24" fill="#7a828b"><rect x="3" y="3" width="18" height="18"/></svg>Subject</div>
      <div class="field"><svg width="12" height="12" viewBox="0 0 24 24" fill="#7a828b"><rect x="6" y="2" width="12" height="20" rx="2"/></svg>Phone Number</div>
      <div class="field"><svg width="12" height="12" viewBox="0 0 24 24" fill="#7a828b"><path d="M2 5h20v14H2z"/></svg>Email Address</div>
      <div class="field message">Message</div>
      <button class="submit" type="button">SUBMIT</button>
    </form>
    <div class="contact-info">
      <p class="lead">Have any questions? Looking for help? Contact us.</p>
      <div class="contact-line"><svg width="18" height="18" viewBox="0 0 24 24" fill="#7a828b"><path d="M12 2a7 7 0 0 1 7 7c0 5-7 13-7 13S5 14 5 9a7 7 0 0 1 7-7z"/><circle cx="12" cy="9" r="2.5" fill="#fff"/></svg>Lorem ipsum dolor, sit amet, Lorem ipsum 123</div>
      <div class="contact-line"><svg width="18" height="18" viewBox="0 0 24 24" fill="#7a828b"><path d="M6 2l4 4-2 3c1 3 4 6 7 7l3-2 4 4-3 4C10 22 2 14 2 5z"/></svg>(407) 555-0164</div>
      <div class="contact-line"><svg width="18" height="18" viewBox="0 0 24 24" fill="#7a828b"><path d="M2 5h20v14H2z"/><path d="M2 5l10 8 10-8" fill="none" stroke="#fff" stroke-width="2"/></svg>Marisol@TRELVOXstudio.example</div>
    </div>
  </div>
</section>

<footer class="site-footer">
  <div class="social" aria-label="Social media links"><span></span><span></span><span></span></div>
  <div class="footer-bar"><span>Privacy Policy | Sitemap</span><span>Copyright © 2014 TRELVOX Studio. All Rights Reserved.</span></div>
</footer>

</body>
</html>
```